update of B2B website and conversion to single page

The current website needs to be modernized. I want what is commonly called a single page website. It is not actually a single page. See some examples here:
https://www.plivenor.example/
https://www.quorbel.example/
https://www.trindavex.example/
Most or all graphics will be replaced.
Please see the attached spreadsheet for a rough draft of the home page layout. Convert the existing website at https://www.zolvarin.example/ to a single page website. We will provide the page content. You will provide all of the design, graphics, development, production deployment. etc. The look and feel should be corporate, polished, premium.

```html
<!DOCTYPE html>
<html lang="en">
<head>
<meta charset="utf-8">
<title>Zolvarin Data – Enterprise Data Quality</title>
<link href="https://fonts.googleapis.com/css2?family=Open+Sans:wght@400;600;700&display=swap" rel="stylesheet">
<style>
:root{
  --navy:#2b3f8c;
  --navy-deep:#233578;
  --ink:#2a2f3a;
  --muted:#6f7683;
  --light:#eef0f4;
  --grey-band:#e4e6ea;
  --gold:#f4b41a;
  --white:#ffffff;
}
*{margin:0;padding:0;box-sizing:border-box}
html,body{width:1200px;height:3740px;overflow:hidden}
body{font-family:"Open Sans",Arial,sans-serif;color:var(--ink);background:var(--white);position:relative}
.photo{position:absolute}

/* header */
.site-header{position:absolute;left:0;top:0;width:1200px;height:112px;background:var(--white)}
.brand{position:absolute;left:100px;top:28px;display:flex;align-items:center;gap:14px}
.brand-mark{width:30px;height:30px;background:var(--navy)}
.brand-name{font-size:32px;font-weight:600;color:var(--navy);line-height:1}
.brand-tag{position:absolute;left:144px;top:68px;font-size:11px;color:var(--muted)}
.main-nav{position:absolute;right:100px;top:74px;display:flex;gap:24px;font-size:12px;font-weight:600;color:var(--ink)}
.login-btn{position:absolute;right:100px;top:28px;width:80px;height:30px;border-radius:15px;background:var(--gold);color:var(--white);font-size:12px;font-weight:600;text-align:center;line-height:30px}

/* hero */
.hero{left:0;top:112px;width:1200px;height:508px;background:linear-gradient(160deg,#c9ccd0 0%,#8f8a84 45%,#5a534c 100%)}
.hero-title{position:absolute;left:0;top:318px;width:1200px;text-align:center;color:var(--white);font-size:46px;line-height:60px;font-weight:700;letter-spacing:1px}
.hero-sub{position:absolute;left:0;top:386px;width:1200px;text-align:center;color:var(--white);font-size:24px;line-height:32px;font-weight:600}

/* about */
.about{position:absolute;left:0;top:620px;width:1200px;height:450px;background:var(--light)}
.about-photo{left:160px;top:80px;width:415px;height:290px;background:linear-gradient(135deg,#dfe7f2,#9fb3cf)}
.about-body{position:absolute;left:600px;top:90px;width:470px}
.section-h{font-size:30px;font-weight:600;color:var(--ink);letter-spacing:1px}
.about-body p{font-size:12.5px;line-height:20px;color:var(--muted);margin-top:16px}
.learn-more{display:inline-block;margin-top:10px;font-size:12px;font-weight:600;color:var(--gold)}

/* mission band */
.mission{position:absolute;left:0;top:1070px;width:1200px;height:440px;background:var(--navy)}
.mission h2{position:absolute;top:70px;width:1200px;text-align:center;color:var(--white);font-size:28px;font-weight:600;letter-spacing:1px}
.mission .lead{position:absolute;top:118px;width:1200px;text-align:center;color:#c9d0ea;font-size:13px}
.stat{position:absolute;top:180px;width:300px;text-align:center;color:var(--white)}
.stat svg{display:block;margin:0 auto}
.stat p{font-size:18px;line-height:26px;margin-top:24px}

/* services */
.services{position:absolute;left:0;top:1510px;width:1200px;height:640px;background:var(--white)}
.centered-h{position:absolute;width:1200px;text-align:center}
.services .sub,.connectors .sub{font-size:12.5px;color:var(--muted)}
.service-card{position:absolute;top:185px;width:472px;height:365px;border:4px solid #1c2130}
.service-card.dq{left:118px;background:linear-gradient(160deg,#4a4f58,#1d222c)}
.service-card.mdm{left:613px;background:linear-gradient(160deg,#dfe4ea,#7e8a98)}
.card-caption{position:absolute;left:24px;bottom:24px;width:290px;color:var(--white)}
.card-caption h3{font-size:20px;font-weight:600}
.card-caption p{font-size:11px;line-height:16px;margin-top:6px;color:#dde2ea}
.read-more{position:absolute;right:24px;bottom:36px;width:110px;height:34px;border-radius:17px;background:var(--navy);color:var(--white);font-size:13px;font-weight:600;text-align:center;line-height:34px}

/* connectors */
.connectors{position:absolute;left:0;top:2150px;width:1200px;height:850px;background:var(--grey-band)}
.tile{position:absolute;width:310px;height:245px}
.apps-tile{background:var(--navy-deep);color:var(--white);padding:34px 30px}
.apps-tile h3{font-size:20px;font-weight:600;margin-bottom:16px}
.apps-tile li{list-style:none;font-size:14px;line-height:24px}
.apps-tile li::before{content:"\25B8";margin-right:8px}

/* contact */
.contact{position:absolute;left:0;top:3000px;width:1200px;height:380px}
.map-area{left:0;top:0;width:1200px;height:380px;background:linear-gradient(135deg,#eceeef,#d9dcdf)}
.contact-form{position:absolute;left:140px;top:30px;width:432px}
.contact-form h2{font-size:34px;font-weight:600;color:var(--navy);letter-spacing:1px;margin-bottom:14px}
.field{height:34px;background:var(--white);border:1px solid #c9cdd3;margin-bottom:10px;font-size:11px;color:var(--muted);padding:10px}
.field.message{height:92px}
.send-btn{height:38px;background:var(--navy);color:var(--white);font-size:13px;font-weight:600;text-align:center;line-height:38px}
.map-pin{position:absolute;left:870px;top:190px;text-align:center;width:110px}
.map-pin span{display:block;font-size:14px;font-weight:600;color:var(--navy)}

/* footer */
.site-footer{position:absolute;left:0;top:3380px;width:1200px;height:360px;background:var(--navy)}
.social{position:absolute;left:0;top:60px;width:1200px;display:flex;justify-content:center;gap:16px}
.social i{display:block;width:48px;height:48px;border-radius:50%;border:2px solid var(--white)}
.footer-nav{position:absolute;top:268px;width:1200px;display:flex;justify-content:center;gap:26px;font-size:12px;font-weight:600;color:var(--white)}
.copyright{position:absolute;top:298px;width:1200px;text-align:center;font-size:11px;color:#c9d0ea}
</style>
</head>
<body>

<header class="site-header">
  <div class="brand"><span class="brand-mark"></span><span class="brand-name">Zolvarin Data</span></div>
  <div class="brand-tag">Enterprise Data Quality Made Easy</div>
  <a class="login-btn">LOGIN</a>
  <nav class="main-nav"><span>ABOUT US</span><span>BENEFITS</span><span>OUR SERVICES</span><span>CONNECTORS</span><span>CONTACT US</span></nav>
</header>

<section class="photo hero" role="img" aria-label="Hands working on a laptop and tablet at a desk">
  <h1 class="hero-title">DATA QUALITY PROOF OF CONCEPT</h1>
  <p class="hero-sub">Flexible Deployment Options</p>
</section>

<section class="about">
  <div class="photo about-photo" role="img" aria-label="Business person using a tablet with charts"></div>
  <div class="about-body">
    <h2 class="section-h">ABOUT US</h2>
    <p>Sed ut perspiciatis unde omnis iste natus error sit voluptatem accusantium doloremque laudantium, totam rem aperiam, eaque ipsa quae ab illo inventore veritatis et quasi architecto beatae vitae dicta sunt explicabo. Nemo enim ipsam voluptatem quia voluptas sit aspernatur aut odit aut fugit.</p>
    <p>At vero eos et accusamus et iusto odio dignissimos ducimus qui blanditiis praesentium voluptatum deleniti atque corrupti quos dolores et quas molestias excepturi sint occaecati cupiditate non provident, similique sunt in culpa.</p>
    <a class="learn-more">Learn more</a>
  </div>
</section>

<section class="mission">
  <h2>ZOLVARIN DATA</h2>
  <p class="lead">Enterprise Data Quality and Master Data Management Made Easy</p>
  <div class="stat" style="left:150px">
    <svg width="64" height="64" viewBox="0 0 64 64"><circle cx="32" cy="32" r="30" fill="var(--gold)"/><path d="M18 22h12v22H18zM34 22h12v22H34z" fill="none" stroke="#fff" stroke-width="3"/></svg>
    <p>Cleanse addresses<br>in 5 minutes</p>
  </div>
  <div class="stat" style="left:450px">
    <svg width="64" height="64" viewBox="0 0 64 64"><circle cx="32" cy="32" r="30" fill="var(--gold)"/><path d="M16 24h18l6 8-6 8H16M48 32H38" fill="none" stroke="#fff" stroke-width="3"/></svg>
    <p>Match &amp; Merge records<br>in 10 minutes</p>
  </div>
  <div class="stat" style="left:750px">
    <svg width="64" height="64" viewBox="0 0 64 64"><circle cx="32" cy="32" r="30" fill="var(--gold)"/><rect x="22" y="18" width="22" height="28" fill="none" stroke="#fff" stroke-width="3"/><path d="M16 32h16m-5-5 5 5-5 5" fill="none" stroke="#fff" stroke-width="3"/></svg>
    <p>Master records in<br>60 minutes</p>
  </div>
</section>

<section class="services">
  <h2 class="centered-h section-h" style="top:90px">OUR SERVICES</h2>
  <p class="centered-h sub" style="top:138px">Sed ut perspiciatis unde omnis iste natus error sit voluptatem accusant</p>
  <article class="service-card dq" role="img" aria-label="Hands on a laptop with glowing data icons">
    <div class="card-caption"><h3>DATA QUALITY</h3><p>Lorem ipsum dolor sit amet, consectetur adipiscing elit, sed do eiusmod tempor incididunt.</p></div>
    <a class="read-more">Read More</a>
  </article>
  <article class="service-card mdm" role="img" aria-label="Person pointing at a project timeline on a screen">
    <div class="card-caption"><h3>MASTER DATA MANAGEMENT</h3><p>Lorem ipsum dolor sit amet, consectetur adipiscing elit, sed do eiusmod tempor incididunt.</p></div>
    <a class="read-more">Read More</a>
  </article>
</section>

<section class="connectors">
  <h2 class="centered-h section-h" style="top:150px">RICH CONNECTORS</h2>
  <p class="centered-h sub" style="top:196px">Duis aute irure dolor in reprehenderit in voluptate velit esse</p>
  <div class="tile apps-tile" style="left:115px;top:230px">
    <h3>Applications</h3>
    <ul><li>Trindavex</li><li>Mellowcrest CRM</li><li>Ardenvale</li><li>Corvant Business Suite</li></ul>
  </div>
  <div class="photo tile" style="left:445px;top:230px;background:linear-gradient(180deg,#2e4a63,#8fb3c9)" role="img" aria-label="Server room corridor"></div>
  <div class="photo tile" style="left:775px;top:230px;background:linear-gradient(135deg,#f0f4f7,#bcd0de)" role="img" aria-label="Hand touching a digital interface"></div>
  <div class="photo tile" style="left:115px;top:495px;background:linear-gradient(135deg,#e8eef6,#a8bedb)" role="img" aria-label="Financial bar charts on paper"></div>
  <div class="photo tile" style="left:445px;top:495px;background:linear-gradient(135deg,#d8c7ae,#8b7660)" role="img" aria-label="Team reviewing reports on a desk"></div>
  <div class="photo tile" style="left:775px;top:495px;background:linear-gradient(135deg,#c9c3bd,#5e5650)" role="img" aria-label="Hands typing on a laptop"></div>
</section>

<section class="contact">
  <div class="photo map-area" role="img" aria-label="Street map showing the office location"></div>
  <form class="contact-form">
    <h2>CONTACT US</h2>
    <div class="field">Enter Your Name</div>
    <div class="field">Enter Your Email</div>
    <div class="field message">Message</div>
    <div class="send-btn">SEND MESSAGE</div>
  </form>
  <div class="map-pin">
    <svg width="26" height="36" viewBox="0 0 26 36"><path d="M13 0C6 0 0 6 0 13c0 10 13 23 13 23s13-13 13-23C26 6 20 0 13 0z" fill="var(--navy)"/><circle cx="13" cy="13" r="5" fill="#fff"/></svg>
    <span>ZOLVARIN DATA</span>
  </div>
</section>

<footer class="site-footer">
  <div class="social" aria-label="Social links"><i></i><i></i><i></i><i></i></div>
  <nav class="footer-nav"><span>ABOUT US</span><span>BENEFITS</span><span>OUR SERVICES</span><span>CONNECTORS</span><span>CONTACT US</span></nav>
  <p class="copyright">Copyright © 2016 All rights reserved. Privacy policy</p>
</footer>

</body>
</html>
```